Kestrel Facilities Business Card Design

We would now like to design business cards with the new Kestrel Facilities logo

Target Market(s)

Professional

Industry/Entity Type

Professional services

Contact Information for Business Card

Employee name, title, phone number, email address, corporate office address and logo.

Font styles to use
Sans Serif

Colors
0054AA
0677BA
7BADD7
CADEEF
E8F1F8

Requirements
Must have
• My logo
Should not have
• any other pictures or images besides my logo

```html
<!DOCTYPE html>
<html lang="en">
<head>
<meta charset="utf-8">
<title>Kestrel Facilities Business Card</title>
<link rel="stylesheet" href="https://fonts.googleapis.com/css2?family=Open+Sans:wght@400;600;700&display=swap">
<style>
  :root {
    --page-bg: #3a3a3b;
    --card-bg: #1b1b1d;
    --card-back-dark: #111113;
    --card-back-light: #2a2a2d;
    --brand-blue: #3a7fd3;
    --text-light: #e6e6e6;
  }
  * { box-sizing: border-box; margin: 0; padding: 0; }
  html, body { width: 1200px; height: 801px; overflow: hidden; }
  body {
    background: var(--page-bg);
    font-family: "Open Sans", Arial, sans-serif;
    display: flex;
    align-items: center;
    justify-content: center;
    gap: 40px;
  }
  .card {
    position: relative;
    width: 520px;
    height: 300px;
    border-bottom: 3px solid var(--brand-blue);
    box-shadow: 0 14px 30px rgba(0,0,0,.35);
    overflow: hidden;
  }
  .card-front { background: var(--card-bg); }

  .brand-name {
    position: absolute;
    top: 46px;
    right: 40px;
    display: flex;
    align-items: center;
    gap: 12px;
    color: var(--brand-blue);
    font-weight: 700;
    font-size: 22px;
    letter-spacing: .5px;
    text-transform: uppercase;
    line-height: 1;
    white-space: nowrap;
  }
  .brand-square {
    width: 26px;
    height: 26px;
    background: var(--brand-blue);
  }
  .person { position: absolute; left: 40px; top: 122px; }
  .person-name {
    color: var(--brand-blue);
    font-weight: 700;
    font-size: 19px;
    text-transform: uppercase;
    line-height: 1.1;
    white-space: nowrap;
  }
  .person-title { color: var(--text-light); font-size: 13px; margin-top: 2px; }

  .divider {
    position: absolute;
    left: 40px;
    right: 40px;
    top: 170px;
    height: 1px;
    background: var(--brand-blue);
  }

  .contact-list {
    position: absolute;
    left: 40px;
    top: 190px;
    list-style: none;
    color: var(--text-light);
    font-size: 13px;
    line-height: 22px;
  }
  .contact-list li { display: flex; align-items: center; gap: 8px; white-space: nowrap; }
  .contact-list svg { width: 11px; height: 11px; fill: var(--brand-blue); flex: none; }

  .address {
    position: absolute;
    right: 40px;
    top: 190px;
    text-align: right;
    color: var(--text-light);
    font-size: 13px;
    line-height: 20px;
    font-style: normal;
    white-space: nowrap;
  }

  .card-back {
    background: linear-gradient(120deg, var(--card-back-dark) 0%, var(--card-back-light) 55%, var(--card-back-dark) 100%);
  }
  .pattern-field { position: absolute; inset: 0; }
  .back-brand {
    position: absolute;
    right: 60px;
    top: 130px;
    color: var(--brand-blue);
    font-weight: 700;
    font-size: 20px;
    text-transform: uppercase;
    letter-spacing: .5px;
    white-space: nowrap;
  }
</style>
</head>
<body>

  <section class="card card-front">
    <div class="brand-name"><span class="brand-square"></span>Kestrel Facilities</div>

    <div class="person">
      <p class="person-name">Dana Whitfield</p>
      <p class="person-title">CEO</p>
    </div>

    <div class="divider"></div>

    <ul class="contact-list">
      <li>
        <svg viewBox="0 0 24 24" aria-hidden="true"><path d="M6.6 10.8a15 15 0 0 0 6.6 6.6l2.2-2.2a1 1 0 0 1 1-.25 11.4 11.4 0 0 0 3.6.57 1 1 0 0 1 1 1V20a1 1 0 0 1-1 1A17 17 0 0 1 3 4a1 1 0 0 1 1-1h3.5a1 1 0 0 1 1 1c0 1.25.2 2.45.57 3.57a1 1 0 0 1-.25 1z"/></svg>
        555-014-2280
      </li>
      <li>
        <svg viewBox="0 0 24 24" aria-hidden="true"><path d="M2 5h20v14H2zm2 2v.5l8 5 8-5V7l-8 5z"/></svg>
        dwhitfield@kestrelfacilities.com
      </li>
      <li>
        <svg viewBox="0 0 24 24" aria-hidden="true"><circle cx="12" cy="12" r="10"/></svg>
        www.kestrelfacilities.com
      </li>
    </ul>

    <address class="address">
      1180 Harbor Lane<br>
      Millbrook, MA 317
    </address>
  </section>

  <section class="card card-back">
    <div class="pattern-field" role="img" aria-label="Tone-on-tone repeating brand pattern across the card back"></div>
    <div class="back-brand">Kestrel Facilities</div>
  </section>

</body>
</html>
```